Redesign website for small print company

Vindurgata is a small printing company in Iceland mainly servicing Students, schools, etc. We are also doing all kind of other jobs, like business cards, book printing, brochure printing etc. We are also selling books online.
Our website is: www.vindurgata.is
What we are looking for is:
- Web Design (Uncoded - PSD layout only)
- Mobile friendly design, using our current color scheme: Red, green, yellow and light gray.
- Clean simple design
- Simple, light and easy to use.
- More menu Items/drop down
Industry/Entity Type
Digital Printing
Number of Pages Required
5+ page
Requirements
Must have
- Easy navigation
- Designed for mobile
- Current color scheme (see logo)
Nice to have
- Icon based products

```html
<!DOCTYPE html>
<html lang="en">
<head>
<meta charset="utf-8">
<title>Vindurgata – Printing Services</title>
<link href="https://fonts.googleapis.com/css2?family=Roboto:wght@400;500;700&family=Open+Sans:ital,wght@0,400;0,600;0,700;1,400&display=swap" rel="stylesheet">
<style>
:root{
  --red:#e4232a;
  --yellow:#f6c400;
  --amber:#f5b000;
  --green:#1d6b33;
  --dark-green:#14532a;
  --ink:#1e1e1e;
  --muted:#777;
  --light:#f1f1f1;
  --footer:#efefef;
  --white:#fff;
}
*{margin:0;padding:0;box-sizing:border-box}
html,body{width:1200px;height:3255px;overflow:hidden}
body{position:relative;font-family:"Open Sans",Arial,sans-serif;color:var(--ink);background:var(--white)}
.abs{position:absolute}
a{color:inherit;text-decoration:none}

.topbar{left:0;top:0;width:1200px;height:39px;background:var(--amber);color:var(--white);font-size:14px;font-weight:600}
.topbar span{position:absolute;top:10px;display:flex;align-items:center;gap:6px}
.topbar svg{width:14px;height:14px}

.hero{left:0;top:39px;width:1200px;height:700px;background:linear-gradient(110deg,#ece9e4 0%,#d9c9b8 30%,#e8e4de 55%,#f4f3f1 100%)}
.nav{left:0;top:39px;width:1200px;height:110px}
.logo{position:absolute;left:120px;top:40px;display:flex;align-items:center;gap:12px;font-family:"Roboto",sans-serif;font-weight:700;font-size:30px;color:var(--ink);letter-spacing:.5px}
.logo i{display:block;width:38px;height:38px;background:var(--red)}
.menu{position:absolute;left:490px;top:44px;display:flex;gap:34px;font-family:"Roboto",sans-serif;font-size:19px;color:#333}
.cart{position:absolute;left:1022px;top:37px;width:40px;height:40px;border-radius:50%;background:var(--green);display:flex;align-items:center;justify-content:center}

.hero-badge{left:655px;top:163px;width:426px;height:426px;border-radius:50%;border:6px solid var(--green);padding:10px}
.hero-badge div{width:100%;height:100%;border-radius:50%;background:var(--red);display:flex;flex-direction:column;align-items:center;justify-content:center;text-align:center}
.hero-badge h1{font-family:"Roboto",sans-serif;font-weight:500;font-size:35px;line-height:37px;color:var(--white);margin-bottom:22px}
.btn-yellow{background:var(--yellow);color:var(--white);font-family:"Roboto",sans-serif;font-weight:500;font-size:20px;padding:14px 46px;border-radius:30px}

h2.section{position:absolute;width:1200px;text-align:center;font-family:"Roboto",sans-serif;font-weight:500;font-size:30px}

.about-title{left:128px;top:815px;font-family:"Roboto",sans-serif;font-weight:500;font-size:36px}
.about-text{left:128px;top:880px;width:465px;font-size:16.5px;line-height:26px;color:var(--muted)}
.btn-green{left:127px;top:1089px;width:165px;height:44px;border-radius:24px;background:var(--green);color:var(--white);font-weight:600;font-size:15px;display:flex;align-items:center;justify-content:center}
.about-art{left:598px;top:780px;width:478px;height:385px;border-radius:6px;background:linear-gradient(135deg,#6fb2a0 0%,#9cc7a8 45%,#e7c34a 85%,#f0d36a 100%)}

.products{left:0;top:1240px;width:1200px;height:560px;background:var(--red);color:var(--white)}
.product{position:absolute;top:1420px;width:225px}
.product svg{width:60px;height:76px}
.product h3{font-family:"Roboto",sans-serif;font-weight:500;font-size:20px;line-height:26px;margin-top:14px}
.product p{font-size:12.5px;line-height:20px;margin-top:12px}
.btn-line{display:inline-flex;align-items:center;justify-content:center;width:132px;height:36px;border:2px solid var(--white);border-radius:20px;font-size:12px;font-weight:600;margin-top:18px}

.work{left:0;top:1866px;width:1200px;height:414px;background:linear-gradient(#fff 0%,#ececec 100%)}
.work-photo{position:absolute;top:1920px;width:262px;height:262px;border-radius:50%;border:3px solid #cfcfcf;background:radial-gradient(circle,#e6e6e6 0%,#b9b9b9 100%)}
.chev{position:absolute}

.card{position:absolute;top:2430px;width:282px;height:178px;background:var(--white);border-radius:4px;box-shadow:0 4px 14px rgba(0,0,0,.12);padding:26px 22px 0 26px;display:flex;gap:8px}
.card b{font-family:Georgia,serif;font-size:40px;line-height:34px;color:var(--yellow)}
.card p{font-style:italic;font-size:13px;line-height:22px;color:#555}
.author{position:absolute;top:2622px;display:flex;align-items:center;gap:12px}
.author i{display:block;width:46px;height:46px;border-radius:50%;background:linear-gradient(#cdbba6,#8f7b6a)}
.author strong{display:block;font-size:14px;font-weight:600;color:#333}
.author small{font-size:12px;color:#888}

.footer{left:0;top:2860px;width:1200px;height:330px;background:var(--footer)}
.fcol{position:absolute;top:2918px}
.fcol h4{font-family:"Roboto",sans-serif;font-weight:500;font-size:19px;margin-bottom:14px}
.fcol li{list-style:none;font-size:14.5px;line-height:31px;color:#333}
.social{display:flex;gap:8px;margin-top:12px}
.social i{display:block;width:28px;height:28px;border-radius:50%;background:#3166a8}
.map{left:749px;top:2912px;width:335px;height:210px;background:linear-gradient(135deg,#d9d9d9,#c6c6c6 60%,#dedede)}
.copy{left:0;top:3190px;width:1200px;height:65px;background:#e2e2e2;text-align:center;line-height:65px;font-size:14px;color:#666}
</style>
</head>
<body>

<div class="abs topbar">
  <span style="left:130px"><svg viewBox="0 0 16 16" fill="none" stroke="#fff" stroke-width="2.2"><circle cx="6.5" cy="6.5" r="4.8"/><path d="M10 10l4.5 4.5"/></svg>Search Product</span>
  <span style="left:457px"><svg viewBox="0 0 16 16" fill="#fff"><path d="M3 1l3 3-1.5 2a9 9 0 0 0 5.5 5.5L12 10l3 3-2 2C7 15 1 9 1 3z"/></svg>Phone: 555 0142</span>
  <span style="left:640px"><svg viewBox="0 0 16 16" fill="#fff"><path d="M1 3h14v10H1z"/><path d="M1 3l7 6 7-6" stroke="#f5b000" stroke-width="1.5" fill="none"/></svg>verk@vindurgata.is</span>
  <span style="left:824px"><svg viewBox="0 0 16 16" fill="none" stroke="#fff" stroke-width="2"><circle cx="8" cy="8" r="6.5"/><path d="M8 4v4l3 2"/></svg>Mon - Fri 9-17</span>
</div>

<div class="abs hero" role="img" aria-label="Photo of a student reading and studying at a desk"></div>

<header class="abs nav">
  <div class="logo"><i></i>VINDURGATA</div>
  <nav class="menu">
    <a>About Us</a><a>Product &#8964;</a><a>Submission of Works</a><a>Contact</a>
  </nav>
  <div class="cart"><svg width="20" height="18" viewBox="0 0 20 18" fill="#fff"><path d="M1 1h3l2 10h11l2-7H6" stroke="#fff" stroke-width="2" fill="none"/><circle cx="8" cy="15" r="2"/><circle cx="16" cy="15" r="2"/></svg></div>
</header>

<div class="abs hero-badge"><div>
  <h1>PRINTING SERVICES<br>FOR STUDENTS<br>&amp; SCHOOL</h1>
  <a class="btn-yellow">View Services</a>
</div></div>

<svg class="abs" style="left:0;top:600px" width="1200" height="170" viewBox="0 0 1200 170">
  <path d="M0 55 C250 10 420 150 700 95 C900 55 1050 20 1200 40 L1200 170 L0 170Z" fill="var(--yellow)"/>
  <path d="M0 40 C250 0 420 130 700 80 C900 40 1050 0 1200 20 L1200 60 C1050 40 900 75 700 110 C420 165 250 30 0 72Z" fill="var(--red)"/>
  <path d="M0 72 C250 30 420 165 700 110 C900 75 1050 40 1200 60 L1200 170 L0 170Z" fill="#fff"/>
  <path d="M0 100 C250 60 420 190 700 140 C900 100 1050 70 1200 85 L1200 170 L0 170Z" fill="#fff"/>
</svg>

<h2 class="abs about-title">ABOUT VINDURGATA</h2>
<p class="abs about-text">University education is a company located in the campus, which has specialized in the service of school staff, as well as providing general public printing.<br>Higher education publishes seminars and first-class textbooks for courses, prints theses for lesson, as well as working on an unprecedented number of smaller pieces for students, teachers and organizations.</p>
<a class="abs btn-green">Learn More</a>
<div class="abs about-art" role="img" aria-label="Printed brochures and business cards with a cycling illustration"></div>

<svg class="abs" style="left:0;top:1190px" width="1200" height="60" viewBox="0 0 1200 60">
  <path d="M0 0 C150 50 400 70 650 45 C850 25 1050 0 1200 10 L1200 60 L0 60Z" fill="var(--red)"/>
  <path d="M560 48 C800 20 1050 -2 1200 10 L1200 28 C1050 14 820 28 560 48Z" fill="var(--yellow)"/>
  <path d="M700 38 C900 10 1080 -5 1200 0 L1200 12 C1060 4 880 22 700 38Z" fill="var(--green)"/>
</svg>

<section class="abs products">
  <h2 class="section" style="top:88px;color:var(--white)">OUR PRODUCTS</h2>
</section>

<div class="product" style="left:114px;color:#fff">
  <svg viewBox="0 0 60 76" fill="none" stroke="#fff" stroke-width="3"><rect x="4" y="4" width="52" height="68" rx="3"/><path d="M14 4v68"/><path d="M24 4v22l6-5 6 5V4"/></svg>
  <h3>BOOK<br>PRINTING</h3>
  <p>Class aptent taciti sociosqu ad litora torquent per conubia nostra per inceptos hymenaeos Proin</p>
  <a class="btn-line">Learn More</a>
</div>
<div class="product" style="left:370px;color:#fff">
  <svg viewBox="0 0 76 76" style="width:76px" fill="none" stroke="#fff" stroke-width="3"><path d="M4 10l22-6 24 6 22-6v62l-22 6-24-6-22 6z"/><path d="M26 4v62M50 10v62"/><path d="M10 22h10M10 32h10M32 24h12M32 34h12M56 22h10M56 32h10"/></svg>
  <h3>BROCHURE<br>PRINTING</h3>
  <p>Class aptent taciti sociosqu ad litora torquent per conubia nostra per inceptos hymenaeos Proin</p>
  <a class="btn-line">Learn More</a>
</div>
<div class="product" style="left:625px;color:#fff">
  <svg viewBox="0 0 76 76" style="width:76px" fill="none" stroke="#fff" stroke-width="3"><rect x="4" y="14" width="12" height="58"/><rect x="16" y="6" width="14" height="66"/><rect x="30" y="14" width="12" height="58"/><rect x="42" y="4" width="14" height="68"/><rect x="56" y="12" width="14" height="60"/><path d="M4 28h66M4 58h66"/></svg>
  <h3>SELLING<br>BOOKS</h3>
  <p>Class aptent taciti sociosqu ad litora torquent per conubia nostra per inceptos hymenaeos Proin</p>
  <a class="btn-line">Learn More</a>
</div>
<div class="product" style="left:880px;color:#fff">
  <svg viewBox="0 0 76 76" style="width:76px" fill="none" stroke="#fff" stroke-width="3"><rect x="4" y="14" width="68" height="52" rx="3"/><path d="M30 8h16v10H30z"/><circle cx="24" cy="36" r="7"/><path d="M12 56c2-8 22-8 24 0M44 34h20M44 44h20M44 54h14"/></svg>
  <h3>BUSINESS<br>CARDS</h3>
  <p>Class aptent taciti sociosqu ad litora torquent per conubia nostra per inceptos hymenaeos Proin</p>
  <a class="btn-line">Learn More</a>
</div>

<svg class="abs" style="left:0;top:1770px" width="1200" height="100" viewBox="0 0 1200 100">
  <path d="M0 0 H1200 V85 C1000 20 750 30 500 60 C300 80 120 70 0 60Z" fill="var(--red)"/>
  <path d="M0 40 C150 50 300 60 520 58 C300 84 120 80 0 72Z" fill="var(--yellow)"/>
  <path d="M0 60 C150 70 300 68 520 58 C300 92 120 92 0 86Z" fill="var(--green)"/>
  <path d="M0 86 C120 92 300 92 520 58 C750 30 1000 20 1200 85 V100 H0Z" fill="#fff"/>
</svg>

<section class="abs work"></section>
<h2 class="section" style="top:1852px;color:var(--red)">OUR WORK</h2>
<svg class="chev" style="left:118px;top:2022px" width="26" height="52" viewBox="0 0 26 52"><path d="M23 2L3 26l20 24" stroke="#555" stroke-width="3" fill="none"/></svg>
<div class="work-photo" style="left:183px" role="img" aria-label="Photo of printed folded brochures"></div>
<div class="work-photo" style="left:478px" role="img" aria-label="Photo of printed stationery and letterheads"></div>
<div class="work-photo" style="left:781px" role="img" aria-label="Photo of printed business cards and envelope"></div>
<svg class="chev" style="left:1055px;top:2022px" width="26" height="52" viewBox="0 0 26 52"><path d="M3 2l20 24L3 50" stroke="#555" stroke-width="3" fill="none"/></svg>

<h2 class="section" style="top:2348px;color:var(--green)">TESTIMONIALS</h2>
<svg class="chev" style="left:96px;top:2498px" width="20" height="42" viewBox="0 0 20 42"><path d="M18 2L3 21l15 19" stroke="#777" stroke-width="2.5" fill="none"/></svg>
<svg class="chev" style="left:1100px;top:2498px" width="20" height="42" viewBox="0 0 20 42"><path d="M2 2l15 19L2 40" stroke="#777" stroke-width="2.5" fill="none"/></svg>

<div class="card" style="left:156px"><b>&ldquo;</b><p>Morbi diam mauris viverra in gravida eu mattis in ante Morbi eget arcu Morbi porta libero id ullamcorper nonummy nibh ligula pulvinar metus eget</p></div>
<div class="card" style="left:477px"><b>&ldquo;</b><p>Morbi diam mauris viverra in gravida eu mattis in ante Morbi eget arcu Morbi porta libero id ullamcorper nonummy nibh ligula pulvinar metus eget</p></div>
<div class="card" style="left:797px"><b>&ldquo;</b><p>Morbi diam mauris viverra in gravida eu mattis in ante Morbi eget arcu Morbi porta libero id ullamcorper nonummy nibh ligula pulvinar metus eget</p></div>

<div class="author" style="left:166px"><i role="img" aria-label="Author portrait"></i><div><strong>By Author Name</strong><small>City Location</small></div></div>
<div class="author" style="left:487px"><i role="img" aria-label="Author portrait"></i><div><strong>By Author Name</strong><small>City Location</small></div></div>
<div class="author" style="left:807px"><i role="img" aria-label="Author portrait"></i><div><strong>By Author Name</strong><small>City Location</small></div></div>

<svg class="abs" style="left:0;top:2740px" width="1200" height="130" viewBox="0 0 1200 130">
  <path d="M0 70 C250 20 450 100 650 80 C850 60 1000 10 1200 40 V130 H0Z" fill="var(--yellow)"/>
  <path d="M0 60 C250 5 450 80 650 62 C850 45 1000 0 1200 25 V75 C1000 50 850 100 650 115 C450 130 250 70 0 100Z" fill="var(--red)"/>
  <path d="M0 118 C250 80 450 135 650 125 C850 112 1000 80 1200 95 V130 H0Z" fill="var(--footer)"/>
</svg>

<footer class="abs footer"></footer>
<div class="fcol" style="left:128px"><h4>QUICK LINKS</h4><ul><li>Home</li><li>About Us</li><li>Products</li><li>Services</li></ul></div>
<div class="fcol" style="left:325px"><h4>RESOURCES</h4><ul><li>Testimonials</li><li>Submission of works</li><li>Blogs</li><li>Contact Us</li></ul></div>
<div class="fcol" style="left:525px"><h4>CONTACT US</h4><ul><li>verk@vindurgata.is</li><li>Phone: 555 0142</li><li>Mon - Fri: 9-17</li></ul>
  <div class="social"><i></i><i></i><i></i><i></i></div></div>
<div class="abs map" role="img" aria-label="Street map showing the shop location">
  <svg style="position:absolute;left:145px;top:82px" width="22" height="30" viewBox="0 0 22 30"><path d="M11 29C11 29 2 17 2 10a9 9 0 0 1 18 0c0 7-9 19-9 19z" fill="var(--red)"/><circle cx="11" cy="10" r="3.5" fill="#fff"/></svg>
</div>

<div class="abs copy">© 2018 Company Name &nbsp;All right reserved</div>

</body>
</html>
```